A Maverick Business Card for a Maverick Company!

We're a maverick, 'rule breaker' market research company that needs a maverick business card design to suit who we are!

All logos, colours and text are detailed in the attached briefing document.

Note Please ignore the 'Look & Feel' wizard results and refer ONLY to the attached brief.

```html
<!DOCTYPE html>
<html lang="en">
<head>
<meta charset="utf-8">
<title>Brightline Research – Business Card</title>
<link rel="stylesheet" href="https://fonts.googleapis.com/css2?family=Barlow:wght@400;500;600&display=swap">
<style>
  :root {
    --backdrop: #e6e7e8;
    --card-white: #ffffff;
    --ink-dark: #2b2b2b;
    --ink-grey: #6d6e70;
    --brand-red: #e3232b;
    --red-top: #ea2229;
    --red-bottom: #a9121a;
    --on-red: #ffffff;
    --card-shadow: 0 2px 6px rgba(0,0,0,0.18);
  }
  * { box-sizing: border-box; margin: 0; padding: 0; }
  html, body {
    width: 1200px; height: 1200px; overflow: hidden;
    background: var(--backdrop);
    font-family: "Barlow", Arial, sans-serif;
  }
  .card {
    position: absolute; left: 301px; width: 598px; height: 361px;
    box-shadow: var(--card-shadow);
  }
  /* ---------- front ---------- */
  .card-front { top: 215px; background: var(--card-white); }
  .front-mark {
    position: absolute; left: 40px; top: 150px; width: 200px;
    display: flex; align-items: center; gap: 8px;
  }
  .front-mark .dot { width: 14px; height: 14px; border-radius: 50%; background: var(--brand-red); flex: none; }
  .front-mark .mark-name { font-size: 22px; font-weight: 600; color: var(--ink-grey); line-height: 1.1; }
  .divider {
    position: absolute; left: 248px; top: 58px; width: 3px; height: 240px;
    background: linear-gradient(to bottom, rgba(0,0,0,0), rgba(0,0,0,0.16) 50%, rgba(0,0,0,0));
  }
  .details { position: absolute; left: 286px; top: 54px; color: var(--ink-grey); }
  .person-name, .company-name { font-size: 21px; font-weight: 500; color: var(--ink-dark); line-height: 1.2; }
  .person-role, .direct-line, .address { font-size: 14px; line-height: 1.4; }
  .direct-label { color: var(--brand-red); }
  .company-name { margin-top: 14px; }
  .contact-list { list-style: none; margin-top: 26px; font-size: 14px; }
  .contact-list li { display: flex; align-items: center; gap: 4px; height: 19.5px; }
  .contact-list svg { width: 13px; height: 13px; flex: none; }
  /* ---------- back ---------- */
  .card-back {
    top: 624px; color: var(--on-red); text-align: center;
    background: linear-gradient(to bottom, var(--red-top), var(--red-bottom));
  }
  .back-mark {
    position: absolute; left: 0; right: 0; top: 84px;
    display: flex; justify-content: center; align-items: center; gap: 12px;
  }
  .back-mark .dot { width: 22px; height: 22px; border-radius: 50%; background: var(--on-red); }
  .back-mark .mark-name { font-size: 40px; font-weight: 500; letter-spacing: 1px; }
  .tagline { position: absolute; left: 0; right: 0; top: 208px; font-size: 13.5px; line-height: 1.1; }
  .benefits {
    position: absolute; left: 0; right: 0; top: 270px; list-style: none;
    font-size: 16.5px; font-weight: 500; line-height: 22px;
  }
  .benefits li { display: flex; justify-content: center; align-items: center; gap: 5px; }
  .benefits svg { width: 16px; height: 14px; }
</style>
</head>
<body>
  <section class="card card-front">
    <div class="front-mark">
      <span class="dot"></span>
      <span class="mark-name">Brightline Research</span>
    </div>
    <div class="divider"></div>
    <div class="details">
      <p class="person-name">Dana Whitlow</p>
      <p class="person-role">Managing Director</p>
      <p class="direct-line"><span class="direct-label">Direct</span> 0400 555 218</p>
      <p class="company-name">Brightline Research</p>
      <p class="address">Harbourview Business Suites,<br>48 Calder Lane, Northbridge Vic 3999</p>
      <ul class="contact-list">
        <li><svg viewBox="0 0 14 14"><circle cx="7" cy="7" r="6.2" fill="none" stroke="#e3232b" stroke-width="1.4"/><path d="M4.6 4c.6 2.6 2.6 4.8 5.2 5.6l.6-1.2-1.4-.8-.7.7C7.3 7.8 6.4 6.9 5.9 5.9l.7-.7-.8-1.4z" fill="#e3232b"/></svg>1300 555 012</li>
        <li><svg viewBox="0 0 14 14"><circle cx="7" cy="7" r="6.2" fill="none" stroke="#e3232b" stroke-width="1.4"/><rect x="4" y="6" width="6" height="4" fill="#e3232b"/><rect x="5" y="3.8" width="4" height="2" fill="none" stroke="#e3232b"/></svg>03 5550 1947</li>
        <li><svg viewBox="0 0 14 14"><circle cx="7" cy="7" r="6.2" fill="none" stroke="#e3232b" stroke-width="1.4"/><rect x="4" y="4.8" width="6" height="4.4" fill="none" stroke="#e3232b"/><path d="M4 4.8l3 2.6 3-2.6" fill="none" stroke="#e3232b"/></svg>dana@brightlineresearch.com.au</li>
        <li><svg viewBox="0 0 14 14"><circle cx="7" cy="7" r="6.2" fill="none" stroke="#e3232b" stroke-width="1.4"/><ellipse cx="7" cy="7" rx="2.4" ry="6" fill="none" stroke="#e3232b"/><path d="M1 7h12" stroke="#e3232b"/></svg>www.brightlineresearch.com.au</li>
      </ul>
    </div>
  </section>

  <section class="card card-back">
    <div class="back-mark">
      <span class="dot"></span>
      <span class="mark-name">Brightline Research</span>
    </div>
    <p class="tagline">Sharp research without the<br>heavy consultancy price tag</p>
    <ul class="benefits">
      <li><svg viewBox="0 0 16 14"><path d="M1 7.5l4.5 4.5L15 2" fill="none" stroke="#fff" stroke-width="3"/></svg>Custom consumer research – focused, affordable and quick</li>
      <li><svg viewBox="0 0 16 14"><path d="M1 7.5l4.5 4.5L15 2" fill="none" stroke="#fff" stroke-width="3"/></svg>Put solid evidence at the heart of every decision</li>
      <li><svg viewBox="0 0 16 14"><path d="M1 7.5l4.5 4.5L15 2" fill="none" stroke="#fff" stroke-width="3"/></svg>Send us your research questions and we handle the rest</li>
    </ul>
  </section>
</body>
</html>
```